A Spin Above Par Company Brochure

I am the owner of a Mobile Disc Jockey company specializing in weddings. I am looking for a Tri Fold color brochure that is modern and eye catching with the focus being on upscale wedding events. I also want it to be easy to read and not overly cluttered ! I would like it to reflect our website located at aspinabovepar.example
I also have different variations and file types of my logo such as jpeg and png files. I need some good dance floor pics. If you do not have any good stock photos I can look through my photo library. I uploaded a logo and pic I found from one of my videos. Not sure if it is worth anything.
We also do Uplighting and Photo Booths which I would like in the brochure. Much of the text copy needed can be taken from our website if needed. Please refer to the website to see what we do and our style.

Target Market(s)

upscale weddings

Industry/Entity Type

wedding dj entertainment & masters of ceremonies

Requirements
Nice to have
• nice pictures of packed dance floors and people having fun

```html
<!DOCTYPE html>
<html lang="en">
<head>
<meta charset="utf-8">
<title>A Spin Above Par – Tri-Fold Brochure</title>
<link href="https://fonts.googleapis.com/css2?family=Montserrat:wght@400;500;600;700&family=Oswald:wght@400;500&family=Roboto+Slab:wght@400;500;700&display=swap" rel="stylesheet">
<style>
:root{
  --purple:#8b3ea8;
  --purple-light:#a15cbb;
  --purple-dark:#3a0f57;
  --ink:#2f2f35;
  --grey:#5d5d66;
  --soft:#efeef2;
  --page:#e6e6ea;
  --paper:#ffffff;
  --gold:#f2b705;
}
*{box-sizing:border-box;margin:0;padding:0}
html,body{width:1200px;height:2486px;overflow:hidden;background:var(--page)}
body{position:relative;font-family:'Montserrat',sans-serif;color:var(--grey)}
.spread{position:absolute;left:20px;width:1160px;height:820px;background:var(--paper);
  box-shadow:0 18px 40px rgba(0,0,0,.28);padding:14px;display:flex;gap:36px}
.spread--outside{top:393px}
.spread--inside{top:1273px}
.panel{position:relative;width:353px;height:792px}
.abs{position:absolute}
.photo{position:absolute;border:3px solid #fff;box-shadow:0 1px 3px rgba(0,0,0,.2)}
.band{position:absolute;left:0;top:0;width:100%;background:var(--purple)}
.band__title{position:absolute;top:12px;width:100%;text-align:center;color:#fff;
  font-family:'Roboto Slab',serif;font-size:22px;font-weight:500}
.caption{position:absolute;left:8px;right:8px;font-size:12px;line-height:1.4;color:var(--grey)}
.web-bar{position:absolute;left:8px;bottom:12px;display:flex;gap:6px;height:38px}
.web-bar__icon{width:38px;height:38px;background:var(--purple);display:flex;align-items:center;justify-content:center}
.web-bar__url{width:272px;background:var(--purple-dark);color:#fff;font-family:'Roboto Slab',serif;
  font-size:15px;letter-spacing:3px;display:flex;align-items:center;justify-content:center}
/* booking panel */
.booth-block{top:0;height:500px}
.polaroid{position:absolute;background:#fff;padding:7px;box-shadow:0 2px 6px rgba(0,0,0,.35)}
.polaroid div{width:100%;height:100%}
.booth-text{position:absolute;left:12px;right:12px;top:380px;color:#fff;font-size:11px;line-height:1.35;text-align:justify;text-align-last:center}
.book-icon{position:absolute;left:146px;top:474px;width:60px;height:60px;border-radius:50%;background:var(--purple);border:3px solid #fff;display:flex;align-items:center;justify-content:center}
.book-title{position:absolute;top:540px;width:100%;text-align:center;font-weight:700;line-height:1.05}
.book-title .a{color:var(--purple);font-size:20px;display:block}
.book-title .b{color:var(--ink);font-size:19px;display:block}
.contact{position:absolute;left:0;right:0;top:590px;bottom:12px;background:var(--purple);color:#fff;text-align:center}
.contact__name{margin-top:24px;font-family:'Oswald',sans-serif;font-size:24px;font-weight:400}
.contact__icon{width:24px;height:24px;border-radius:50%;background:#fff;margin:8px auto 2px;display:flex;align-items:center;justify-content:center}
.contact__phone{font-size:19px;font-weight:600;letter-spacing:1px}
.contact__small{font-size:12px}
/* cover */
.brand{position:absolute;top:28px;width:100%;display:flex;align-items:center;justify-content:center;gap:12px}
.brand__dot{width:46px;height:46px;border-radius:50%;background:var(--purple)}
.brand__name{font-family:'Oswald',sans-serif;font-size:40px;font-weight:400;color:#6f6f78}
.cover-band{position:absolute;top:528px;left:0;right:0;height:156px;background:var(--purple);
  color:#fff;font-family:'Roboto Slab',serif;font-size:31px;font-weight:500;line-height:1.12;
  text-align:center;display:flex;align-items:center;justify-content:center;letter-spacing:.5px}
.cover-sub{position:absolute;top:692px;width:100%;text-align:center;font-family:'Roboto Slab',serif;font-size:12.5px;color:var(--ink);line-height:1.35}
/* weddings */
.wed-head{position:absolute;left:8px;right:8px;top:270px;font-family:'Roboto Slab',serif;font-size:15.5px;font-weight:500;color:var(--purple-dark);line-height:1.2}
.services{position:absolute;left:8px;right:8px;top:334px;list-style:none}
.services li{display:flex;gap:14px;height:76px}
.services .thumb{flex:0 0 74px;height:60px}
.services h3{font-family:'Roboto Slab',serif;font-weight:500;font-size:15px;color:var(--purple)}
.services p{font-size:10px;line-height:1.3;color:var(--grey)}
/* photo booth */
.backdrop-title{position:absolute;top:514px;width:100%;text-align:center;font-family:'Roboto Slab',serif;font-weight:500;color:var(--purple-dark);font-size:15px}
.backdrops{position:absolute;left:4px;right:4px;top:546px;display:grid;grid-template-columns:repeat(3,1fr);gap:24px 6px}
.backdrop{height:98px;position:relative}
.backdrop__swatch{height:84px;border-bottom:4px solid #bdbdc2}
.backdrop__label{position:absolute;bottom:-10px;right:2px;font-family:'Oswald',sans-serif;font-size:7px;color:var(--ink);letter-spacing:.3px}
/* reviews */
.reviews-body{position:absolute;left:10px;right:10px;top:50px;bottom:12px;background:var(--soft)}
.reviews-count{text-align:center;margin-top:12px;font-family:'Oswald',sans-serif;font-size:30px;color:var(--purple)}
.review{position:relative;margin:6px 8px 0;background:#fff;height:205px;text-align:center;padding:0 10px}
.review__avatar{width:92px;height:92px;border-radius:50%;margin:0 auto;position:relative;top:-4px}
.review__quote{font-family:'Roboto Slab',serif;color:var(--purple);font-size:26px;line-height:.8;height:16px}
.review__text{font-size:10px;line-height:1.3;color:var(--grey);text-align:justify;text-align-last:center}
.review__name{font-weight:700;color:var(--ink);font-size:14px;margin-top:4px}
.review__stars{color:var(--gold);font-size:11px;letter-spacing:1px;line-height:1}
</style>
</head>
<body>

<!-- Outside spread -->
<section class="spread spread--outside">
  <article class="panel">
    <div class="band" style="height:232px"><div class="band__title">Uplighting</div></div>
    <div class="photo" role="img" aria-label="Ballroom with magenta uplighting and round dining tables" style="left:14px;top:52px;width:325px;height:182px;background:linear-gradient(160deg,#b52c8e,#7b1d5a 55%,#e9a7c7)"></div>
    <div class="photo" role="img" aria-label="White ballroom with chandeliers and draped tables" style="left:14px;top:244px;width:158px;height:218px;background:linear-gradient(180deg,#dfe3f2,#9d9ac2 60%,#4a4866)"></div>
    <div class="photo" role="img" aria-label="Reception hall with blue and teal uplighting" style="left:181px;top:244px;width:158px;height:218px;background:linear-gradient(180deg,#1a2a6b,#1b8aa0 60%,#0d2a3a)"></div>
    <div class="photo" role="img" aria-label="Bride and groom in a warmly lit reception room" style="left:14px;top:472px;width:325px;height:176px;background:linear-gradient(150deg,#f6d9a5,#d6a35a 55%,#8f6334)"></div>
    <p class="caption" style="top:664px">Simply put, Uplighting turns ordinary rooms into extraordinary rooms. It adds color and warmth to any room and creates a totally different atmosphere.</p>
    <div class="web-bar"><div class="web-bar__icon"><svg width="18" height="18" viewBox="0 0 20 20" fill="none" stroke="#fff" stroke-width="1.6"><circle cx="10" cy="10" r="8"/><ellipse cx="10" cy="10" rx="3.5" ry="8"/><line x1="2" y1="10" x2="18" y2="10"/></svg></div><div class="web-bar__url">www.aspinabovepar.example</div></div>
  </article>

  <article class="panel">
    <div class="band booth-block">
      <div class="polaroid" style="left:22px;top:20px;width:132px;height:118px;transform:rotate(-7deg)"><div role="img" aria-label="Guests posing with photo booth props" style="background:linear-gradient(135deg,#55607a,#c0394f 50%,#e7c04a)"></div></div>
      <div class="polaroid" style="left:194px;top:24px;width:130px;height:118px;transform:rotate(6deg)"><div role="img" aria-label="Guests in masquerade masks at the photo booth" style="background:linear-gradient(135deg,#8e8f9a,#3d3d48 55%,#d8d0c0)"></div></div>
      <div class="polaroid" style="left:52px;top:178px;width:240px;height:150px;transform:rotate(-2deg)"><div role="img" aria-label="Couple wearing oversized glasses and hats in the photo booth" style="background:linear-gradient(135deg,#d8dbe2,#3f4a66 50%,#77c23a)"></div></div>
      <p class="booth-text">It's no secret photo booths have been a hit at weddings as well as any other event. Our photo booth offers a modern sleek look and is so simple to operate it doesn't need an attendant. However we want you and your guests to have the best experience possible so we provide one as part of our package.</p>
    </div>
    <div class="book-icon"><svg width="28" height="28" viewBox="0 0 24 24" fill="none" stroke="#fff" stroke-width="1.8"><rect x="3" y="5" width="15" height="15" rx="2"/><line x1="3" y1="9" x2="18" y2="9"/><line x1="7" y1="3" x2="7" y2="6"/><line x1="14" y1="3" x2="14" y2="6"/><circle cx="18" cy="18" r="4" fill="var(--purple)"/><path d="M16.3 18l1.2 1.2 2.2-2.3"/></svg></div>
    <h2 class="book-title"><span class="a">BOOK YOUR</span><span class="b">APPOINTMENT TODAY</span></h2>
    <div class="contact">
      <div class="contact__name">A Spin Above Par</div>
      <div class="contact__icon"><svg width="14" height="14" viewBox="0 0 24 24" fill="var(--purple)"><path d="M6.6 10.8a15 15 0 006.6 6.6l2.2-2.2c.3-.3.7-.4 1-.2 1.1.4 2.3.6 3.6.6.6 0 1 .4 1 1V20c0 .6-.4 1-1 1A17 17 0 013 4c0-.6.4-1 1-1h3.5c.6 0 1 .4 1 1 0 1.3.2 2.5.6 3.6.1.3 0 .7-.2 1z"/></svg></div>
      <div class="contact__phone">555.014.2290</div>
      <div class="contact__icon"><svg width="14" height="14" viewBox="0 0 24 24" fill="none" stroke="var(--purple)" stroke-width="2.4"><rect x="3" y="6" width="18" height="12" rx="1"/><path d="M3 7l9 6 9-6"/></svg></div>
      <div class="contact__small">dave@aspinabovepar.example</div>
      <div class="contact__icon"><svg width="14" height="14" viewBox="0 0 20 20" fill="none" stroke="var(--purple)" stroke-width="1.8"><circle cx="10" cy="10" r="8"/><ellipse cx="10" cy="10" rx="3.5" ry="8"/><line x1="2" y1="10" x2="18" y2="10"/></svg></div>
      <div class="contact__small">www.aspinabovepar.example</div>
    </div>
  </article>

  <article class="panel">
    <div class="brand"><span class="brand__dot"></span><span class="brand__name">A Spin Above Par</span></div>
    <div class="abs" role="img" aria-label="Couple's first dance on a fog-covered floor in a purple-lit ballroom" style="left:0;right:0;top:128px;height:400px;background:linear-gradient(180deg,#3a1340,#9c2f8e 45%,#c5a6d4 80%,#eee6f2)"></div>
    <h1 class="cover-band">MODERN,<br>TASTEFUL, &amp; FUN<br>ENTERTAINMENT</h1>
    <p class="cover-sub">Weddings, Corporate Events, Private Parties, any<br>event is better with A Spin Above Par</p>
    <div class="web-bar"><div class="web-bar__icon"><svg width="18" height="18" viewBox="0 0 20 20" fill="none" stroke="#fff" stroke-width="1.6"><circle cx="10" cy="10" r="8"/><ellipse cx="10" cy="10" rx="3.5" ry="8"/><line x1="2" y1="10" x2="18" y2="10"/></svg></div><div class="web-bar__url">www.aspinabovepar.example</div></div>
  </article>
</section>

<!-- Inside spread -->
<section class="spread spread--inside">
  <article class="panel">
    <div class="band" style="height:172px"><div class="band__title">Weddings</div></div>
    <div class="photo" role="img" aria-label="Bride and groom walking down the aisle among guests" style="left:14px;top:52px;width:325px;height:200px;background:linear-gradient(160deg,#e9efe6,#9aa393 50%,#4b4f57)"></div>
    <h2 class="wed-head">WEDDING ENTERTAINMENT PLANNING &amp; COORDINATION THE WAY YOU WANT IT</h2>
    <ul class="services">
      <li><div class="thumb" role="img" aria-label="Wedding ceremony" style="background:linear-gradient(135deg,#c77a8a,#4a2a3a)"></div><div><h3>Wedding Ceremonies</h3><p>We will be happy to provide your ceremony sound system, music and help you with the planning and organizational flow of your ceremony.</p></div></li>
      <li><div class="thumb" role="img" aria-label="Couple dancing on clouds" style="background:linear-gradient(135deg,#b08a7c,#f0e6e2)"></div><div><h3>Dancing on Clouds</h3><p>Want to add that fairy tale romance that will "wow" your guests. Add our dancing on clouds option.</p></div></li>
      <li><div class="thumb" role="img" aria-label="Dance floor lighting" style="background:linear-gradient(135deg,#7a2fa0,#1d0d30)"></div><div><h3>Lighting</h3><p>Uplighting can transform the atmosphere in your room from ordinary to extraordinary! When used with dance floor lighting it creates both energy and atmosphere.</p></div></li>
      <li><div class="thumb" role="img" aria-label="Monogram projected on the dance floor" style="background:linear-gradient(135deg,#c06fae,#3a1840)"></div><div><h3>Monogram Lighting</h3><p>Uplighting can transform the atmosphere in your room from ordinary to extraordinary! When used with dance floor lighting it creates both energy and atmosphere.</p></div></li>
      <li><div class="thumb" role="img" aria-label="Guests at the photo booth" style="background:linear-gradient(135deg,#2c4f8a,#101828)"></div><div><h3>Photo Booth</h3><p>Add more fun and excitement to your event with our photo booth. We offer several back drops and props!</p></div></li>
      <li><div class="thumb" role="img" aria-label="DJ performing at a reception" style="background:linear-gradient(135deg,#6a3d8c,#d08a6a)"></div><div><h3>DJ Entertainment</h3><p>All of our team members are highly trained professional DJs and emcees with their own unique style.</p></div></li>
    </ul>
  </article>

  <article class="panel">
    <div class="band" style="height:172px"><div class="band__title">Photo Booth</div></div>
    <div class="photo" role="img" aria-label="Guests in captain hats and novelty glasses at the photo booth" style="left:14px;top:52px;width:325px;height:206px;background:linear-gradient(135deg,#d9dbe3,#4f5a78 45%,#e4c43f 70%,#6bbf3b)"></div>
    <div class="photo" role="img" aria-label="Group of guests with props at the photo booth" style="left:14px;top:266px;width:160px;height:228px;background:linear-gradient(160deg,#dfe0e6,#3b4e8a 50%,#b23d4a)"></div>
    <div class="photo" role="img" aria-label="Couple posing with a sign at the photo booth" style="left:179px;top:266px;width:160px;height:228px;background:linear-gradient(160deg,#e3e4ea,#c9a9a3 50%,#2b3e6e)"></div>
    <h2 class="backdrop-title">BACKDROP OPTIONS</h2>
    <div class="backdrops">
      <div class="backdrop"><div class="backdrop__swatch" role="img" aria-label="White geometric backdrop" style="background:linear-gradient(135deg,#fafafa,#d8d8dc)"></div><span class="backdrop__label">WHITE GEOMETRIC TEXTURE</span></div>
      <div class="backdrop"><div class="backdrop__swatch" role="img" aria-label="Black and gold art deco backdrop" style="background:linear-gradient(135deg,#1a1a1a,#a88a3a 50%,#1a1a1a)"></div><span class="backdrop__label">ART DECO / GATSBY</span></div>
      <div class="backdrop"><div class="backdrop__swatch" role="img" aria-label="Plain black backdrop" style="background:#0c0c0c"></div><span class="backdrop__label">BLACK</span></div>
      <div class="backdrop"><div class="backdrop__swatch" role="img" aria-label="Silver sequin backdrop" style="background:linear-gradient(135deg,#c9c9cf,#8c8c94 50%,#e6e6ea)"></div><span class="backdrop__label">SILVER SEQUIN</span></div>
      <div class="backdrop"><div class="backdrop__swatch" role="img" aria-label="Green hedge backdrop" style="background:linear-gradient(135deg,#3f7a2a,#1f4a16)"></div><span class="backdrop__label">HEDGE</span></div>
      <div class="backdrop"><div class="backdrop__swatch" role="img" aria-label="Dark wood backdrop with string lights" style="background:linear-gradient(135deg,#4a3526,#1e140d)"></div><span class="backdrop__label">DARK WOOD WITH STRING LIGHTS</span></div>
    </div>
  </article>

  <article class="panel">
    <div class="band" style="height:172px"><div class="band__title">Read our reviews</div></div>
    <div class="reviews-body">
      <div class="reviews-count">400+ REVIEWS</div>
      <div class="review">
        <div class="review__avatar" role="img" aria-label="Wedding couple portrait" style="background:linear-gradient(135deg,#3c6a5a,#d8d2c6)"></div>
        <div class="review__quote">“</div>
        <p class="review__text">Dave is the absolute BEST! From the moment you first speak with him until the end of the wedding night, he makes you feel so comfortable and at ease. He has all the tools to help you plan the exact ceremony or reception that you want. He can literally run the entire reception like an event planner would.</p>
        <div class="review__name">Laura P.</div><div class="review__stars">★★★★★</div>
      </div>
      <div class="review">
        <div class="review__avatar" role="img" aria-label="Bride portrait" style="background:linear-gradient(135deg,#d6a46a,#f3e7d8)"></div>
        <div class="review__quote">“</div>
        <p class="review__text">I am so happy I hired A Spin Above Par for our wedding day! Dave was so fun and easy to work with — he listened to everything I wanted and delivered way above my expectations! Multiple people came up to us during and after the wedding to compliment the DJ.</p>
        <div class="review__name">Megan R.</div><div class="review__stars">★★★★★</div>
      </div>
      <div class="review">
        <div class="review__avatar" role="img" aria-label="Wedding couple portrait" style="background:linear-gradient(135deg,#b0764f,#2f4a7a)"></div>
        <div class="review__quote">“</div>
        <p class="review__text">Nick &amp; Ella were amazing! They are so helpful and personable. We didn't know the ethics of a wedding ceremony or reception, but they (A Spin Above Par) made great suggestions and guided us to what ended up being the most beautiful, organized, and FUN night of our lives!</p>
        <div class="review__name">Hannah S.</div><div class="review__stars">★★★★★</div>
      </div>
    </div>
  </article>
</section>

</body>
</html>
```